Flyer for Dessert Cafe event launch

Hi
We are launching a new initiative at our cafe - this is the plan:
- We will open Saturday nights to serve desserts, tea and coffee and other after dinner deliciousness (no alcohol)
- Customers stop in and enjoy something sweets on the way home from dinner or movies. We'd decorate the garden with fairy lights, candles and lanterns and create a beautiful and relaxing (and romantic) after dinner atmosphere - maybe a little acoustic guitar
- For the menu we are thinking everything from chocolate mousse and cheesecake to tiramisu and dessert mocktails and even sorbet and gelato.
- The dessert cafe would probably trade from 7pm till 11pm.
Please check out www.brelvantable.com for our current branding feel.

We need an A4 flyer designed to promote this new venture.
I want the design to incorporate trees with fairy lights in them - and hearts - as we will be launching on Valentines Day evening (and the heart is part of our branding). Obviously the design needs to be tied in with our current branding - logo attached in various forms I am happy for you to use whichever fits best with your design. I have also attached some images that inspire me for this project - but they don't need to be used.

The following information will need to be included:

On the way home from dinner, or just craving something sweet?
Join us for Dessert!
Unwind - Relax - Indulge
7pm - 11pm every Saturday night
Starting on Valentines Day
All desserts handmade in-house - with love! *** Coffee *** Tea *** Mocktails *** Share platters available ***Gluten Free, Dairy Free and Vegan options *** Take-Away Available
Live Music

2847 Ridgeway Drive, Harlow Flats (five minutes from Selby Point)
(03) 5391 8264
www.brelvantable.com
Please include the Facebook - Twiiter and Instagram Icons

```html
<!DOCTYPE html>
<html lang="en">
<head>
<meta charset="utf-8">
<title>Brelvan Table – Dessert Nights</title>
<link rel="stylesheet" href="https://fonts.googleapis.com/css2?family=Kaushan+Script&family=Arimo:wght@400&display=swap">
<style>
  :root {
    --red: #d5262f;
    --white: #ffffff;
    --night: #1c3a4a;
    --teal: #4d8ea3;
    --mist: #a9c9d2;
    --wood: #2f78a8;
    --warm: #f2c67a;
  }
  * { box-sizing: border-box; margin: 0; padding: 0; }
  html, body { width: 849px; height: 1200px; overflow: hidden; background: #fff; }
  .flyer { position: relative; width: 849px; height: 1200px; overflow: hidden; font-family: "Arimo", Arial, sans-serif; color: var(--white); }
  .backdrop {
    position: absolute; inset: 0;
    background:
      radial-gradient(circle at 15% 82%, rgba(242,198,122,.55), transparent 22%),
      radial-gradient(circle at 80% 18%, rgba(242,198,122,.35), transparent 20%),
      radial-gradient(circle at 40% 35%, rgba(230,160,170,.35), transparent 25%),
      linear-gradient(180deg, #6f9fae 0%, var(--mist) 35%, var(--teal) 55%, var(--wood) 68%, #5d8fa6 78%, var(--night) 100%);
  }
  .brand { position: absolute; left: 50px; top: 44px; display: flex; align-items: center; gap: 10px; }
  .brand-dot { width: 16px; height: 16px; border-radius: 50%; background: var(--white); }
  .brand-name { font-size: 38px; color: var(--white); }
  .teaser { position: absolute; right: 26px; top: 22px; width: 380px; text-align: center; font-size: 34px; line-height: 1.12; text-shadow: 0 2px 6px rgba(0,0,0,.35); }
  .banner { position: absolute; left: 0; right: 0; top: 272px; height: 64px; background: var(--red); display: flex; align-items: center; justify-content: center; padding-right: 80px; }
  .banner h1 { font-family: "Kaushan Script", cursive; font-weight: 400; font-size: 44px; }
  .launch { position: absolute; left: 70px; top: 425px; width: 340px; text-align: center; font-family: "Kaushan Script", cursive; font-size: 50px; line-height: 1.2; color: var(--red); text-shadow: 0 0 6px #fff, 0 0 2px #fff; }
  .hours { position: absolute; left: 50px; top: 650px; width: 380px; text-align: center; text-shadow: 0 2px 8px rgba(0,0,0,.4); }
  .hours .time { font-size: 70px; line-height: 1; }
  .hours .day { font-size: 34px; margin-top: 6px; }
  .offer { position: absolute; left: 504px; top: 467px; width: 262px; height: 530px; background: var(--red); padding: 30px 12px; text-align: center; box-shadow: 0 4px 14px rgba(0,0,0,.3); }
  .offer h2 { font-family: "Kaushan Script", cursive; font-weight: 400; font-size: 38px; line-height: 1.1; }
  .offer .note { font-family: "Kaushan Script", cursive; font-size: 20px; margin: 6px 0 18px; }
  .offer ul { list-style: none; }
  .offer li { font-size: 19px; line-height: 1.2; padding: 11px 0; }
  .heart { font-size: 15px; }
  .contact { position: absolute; left: 50px; top: 1090px; font-size: 17px; line-height: 1.4; font-style: normal; text-shadow: 0 1px 3px rgba(0,0,0,.5); }
  .contact small { font-size: 14px; }
  .social { position: absolute; left: 530px; top: 1106px; display: flex; gap: 16px; }
  .social span { width: 62px; height: 62px; border-radius: 8px; background: var(--white); }
</style>
</head>
<body>
<main class="flyer">
  <div class="backdrop" role="img" aria-label="Night garden with trees strung with glowing fairy lights over a blue wooden table"></div>

  <div class="brand"><span class="brand-dot"></span><span class="brand-name">Brelvan Table</span></div>

  <p class="teaser">On the way<br>home from dinner,<br>or just craving<br>something sweet?</p>

  <div class="banner"><h1>Join us for Dessert !</h1></div>

  <p class="launch">Starting on<br>Valentines Day</p>

  <div class="hours">
    <p class="time">7pm-11pm</p>
    <p class="day">every Saturday night</p>
  </div>

  <section class="offer">
    <h2>All desserts<br>handmade</h2>
    <p class="note">in-house with love!</p>
    <ul>
      <li>Coffee <span class="heart">♥</span> Tea <span class="heart">♥</span> Mocktails</li>
      <li>Share platters available</li>
      <li>Gluten Free <span class="heart">♥</span> Dairy Free<br>and Vegan options</li>
      <li>Take-Away Available</li>
      <li>Unwind <span class="heart">♥</span> Relax <span class="heart">♥</span> Indulge</li>
      <li>Live Music</li>
    </ul>
  </section>

  <address class="contact">
    2847 Ridgeway Drive, Harlow Flats<br>
    <small>(five minutes from Selby Point)</small><br>
    (03) 5391 8264 • www.brelvantable.com
  </address>

  <div class="social" aria-label="Social media links"><span></span><span></span><span></span></div>
</main>
</body>
</html>
```